Logo and Card design for KRV Home Solutions LLC

I need an edgier logo and business card designs. Current logo attached. I like the colors below. I would like the logo to incorporate a home in the design.
Title = Principal-Acquisitions
Email:KRVHOMESOLUTIONS@fernmail.example
555-214-0937
facebook
IG
2 sided business card with the front being contact info a slogan about selling a home fast. The back incorporating What we do. Buy houses, land, or commercial property as is. We find solutions to make the process of selling simple and fair.

Target Market(s)

Motivated house sellers.

Industry/Entity Type

Business

Contact Information for Business Card

Who we are: We are a Faith based Real Estate Investment Company. We pay cash for homes in any condition and can close quick. Whatever the reason you need to sell fast, we can help. We believe in creating win-win solutions to help you in your time of need. We care! We can help!

Logo Text

KRV Home Solutions LLC

Font styles to use
Sans Serif

Colors
33a6d7
0355a3
85abd2
cee9f5
9d9d9d
b2b2b2
ffffff

Requirements
Must have
• Old logo attached. I want something edgier.
• Company name, phone number, description on the back of what we can do. Pay all cash. Buy in as is condition. No fees,Commisions or closing costs.Close quick. No hassles with solutions to meet your unique situation.
• Call today for an offer within 24 hours.

```html
<!DOCTYPE html>
<html lang="en">
<head>
<meta charset="utf-8">
<title>KRV Home Solutions – Business Card</title>
<link rel="stylesheet" href="https://fonts.googleapis.com/css2?family=Roboto:wght@400;500;700&display=swap">
<style>
  :root {
    --page-bg: #e9e6e1;
    --navy: #1e3a6e;
    --navy-deep: #1a3264;
    --photo-blue: #2c4c86;
    --pale-ground: #e6eadb;
    --roof-grey: #6f6f6a;
    --logo-navy: #1f3a70;
    --white: #ffffff;
  }
  * { box-sizing: border-box; margin: 0; padding: 0; }
  html, body {
    width: 1200px; height: 960px; overflow: hidden;
    background: var(--page-bg);
    font-family: "Roboto", Arial, sans-serif;
  }
  .canvas { position: relative; width: 1200px; height: 960px; }

  .card {
    position: absolute; width: 600px; height: 343px; overflow: hidden;
    box-shadow: 0 3px 8px rgba(0,0,0,0.35);
  }
  .card--front { left: 314px; top: 113px; }
  .card--back  { left: 312px; top: 472px; background: var(--navy); color: var(--white); }

  .front-art { position: absolute; inset: 0; }

  .identity { position: absolute; left: 31px; top: 34px; color: var(--white); }
  .identity__name { font-size: 22px; font-weight: 500; letter-spacing: 0.3px; line-height: 26px; }
  .identity__title { font-size: 15px; font-weight: 500; line-height: 20px; margin-bottom: 7px; }
  .contact-list { list-style: none; }
  .contact-list li {
    display: flex; align-items: center; gap: 8px;
    font-size: 14.5px; line-height: 19px;
  }
  .contact-list svg { width: 13px; height: 13px; flex: none; fill: var(--white); }

  .benefits {
    position: absolute; right: 26px; top: 51px; list-style: none;
    color: var(--white); text-align: right; font-size: 13.5px; line-height: 18px;
  }
  .benefits li::after {
    content: ""; display: inline-block; width: 4px; height: 4px; border-radius: 50%;
    background: var(--white); margin-left: 9px; vertical-align: middle;
  }
  .benefits li.no-bullet::after { visibility: hidden; }

  .brand-name {
    position: absolute; left: 0; right: 0; top: 270px; text-align: center;
    font-size: 26px; font-weight: 700; color: var(--logo-navy); letter-spacing: 0.5px;
  }

  .back-brand {
    position: absolute; left: 0; right: 0; top: 92px; text-align: center;
    font-size: 30px; font-weight: 700; letter-spacing: 1px; color: var(--white);
  }
  .back-rule {
    position: absolute; left: 101px; width: 390px; top: 137px; height: 2px; background: var(--white);
  }
  .about { position: absolute; left: 0; right: 0; top: 157px; text-align: center; }
  .about__heading { font-size: 15px; font-weight: 700; line-height: 20px; }
  .about__text { font-size: 14.6px; line-height: 18px; margin-bottom: 11px; }
</style>
</head>
<body>
<main class="canvas">

  <section class="card card--front" aria-label="Business card front">
    <svg class="front-art" width="600" height="343" viewBox="0 0 600 343">
      <defs>
        <linearGradient id="photoTone" x1="0" y1="0" x2="0" y2="1">
          <stop offset="0" stop-color="#2a4a86"/>
          <stop offset="1" stop-color="#34558f"/>
        </linearGradient>
      </defs>
      <rect width="600" height="343" fill="url(#photoTone)" role="img" aria-label="Photograph of a two-storey suburban house with lawn, tinted blue"/>
      <polygon points="0,268 287,162 600,292 600,343 0,343" fill="var(--pale-ground)" role="img" aria-label="Faded photograph of a front lawn and path"/>
      <polyline points="0,262 287,156 600,286" fill="none" stroke="var(--roof-grey)" stroke-width="5"/>
      <polyline points="0,268 287,162 600,292" fill="none" stroke="var(--white)" stroke-width="2"/>
    </svg>

    <div class="identity">
      <h1 class="identity__name">JORDAN VALE</h1>
      <p class="identity__title">Principal-Acquisitions</p>
      <ul class="contact-list">
        <li><svg viewBox="0 0 24 24"><path d="M6.6 10.8a15.1 15.1 0 0 0 6.6 6.6l2.2-2.2c.3-.3.7-.4 1-.2 1.1.4 2.3.6 3.6.6.6 0 1 .4 1 1V20c0 .6-.4 1-1 1C10.6 21 3 13.4 3 4c0-.6.4-1 1-1h3.5c.6 0 1 .4 1 1 0 1.3.2 2.5.6 3.6.1.3 0 .7-.2 1z"/></svg>555-214-0937</li>
        <li><svg viewBox="0 0 24 24"><path d="M2 5h20v14H2zm2 2v.5l8 5 8-5V7zm0 2.9V17h16V9.9l-8 5z"/></svg>KRVHOMESOLUTIONS@fernmail.example</li>
        <li><svg viewBox="0 0 24 24"><circle cx="12" cy="12" r="10"/></svg>KRVHOMESOLUTIONS.example</li>
      </ul>
    </div>

    <ul class="benefits">
      <li>Pay all cash. Buy in as is condition</li>
      <li>No fees,Commisions or closing costs</li>
      <li>Close quick. No hassles with</li>
      <li class="no-bullet">solutions to meet your unique situation</li>
      <li>Call today for an offer within 24 hours</li>
    </ul>

    <p class="brand-name">KRV HOME SOLUTIONS</p>
  </section>

  <section class="card card--back" aria-label="Business card back">
    <p class="back-brand">KRV HOME SOLUTIONS</p>
    <div class="back-rule"></div>
    <div class="about">
      <h2 class="about__heading">WHO WE ARE</h2>
      <p class="about__text">We are a Faith based Real Estate Investment Company. We pay cash for<br>homes in any condition and can close quick. Whatever the reason you need<br>to sell fast, we can help. We believe in creating win-win solutions to help</p>
      <h2 class="about__heading">WHAT WE DO</h2>
      <p class="about__text">Buy houses, land, or commercial property as is.<br>We find solutions to make the process of selling simple and fair.</p>
    </div>
  </section>

</main>
</body>
</html>
```